BrivoTerna. Lantern of the Steady Harvest. Business card

Professional business card for BrivoTerna (Lantern of the Steady Harvest)
My rationale: Strategy-> Execution-> Results-> Value that lead to the BrivoTerna name: We put the Lantern of the Steady Harvest.
We deliver value to our customers helping them at defining a good strategy (cyan arrow). 90% of well formulated strategies fail due to poor execution so we also consider strategical execution very important (green arrow). Due to the execution we obtain the results (blue arrow). Finally, the results provide feedback to redefine strategy, and the new strategy has to be executed and new results obtained providing new feedback and on and on. It's like a wheel that finally, must create corporate value: value for shareholders, staholders, employees, providers...-

Target Market(s)

CEOs and steering comitees , invewrnent funds

Industry/Entity Type

Business Consultant

Contact Information for Business Card

Teodoro Vinsquel
CEO & Founder
teodoro.vinsquel@brivoterna-example.com
Mobile: +34 655.803.912
www.brivoterna-example.com

Colors

Designer to choose colors to be used in the design.

Requirements
Nice to have
• Nice to hace the words: Strategy, execution, results
• Nice to vave the claim: Lantern of the Steady Harvest
• The three colors should be shown:
• cyan for STRATEGY
• green for EXECUTION
• blue for RESULTS
Should not have
• Complete black background

```html
<!DOCTYPE html>
<html lang="en">
<head>
<meta charset="utf-8">
<title>BrivoTerna — Business Card</title>
<link href="https://fonts.googleapis.com/css2?family=Roboto:wght@400;700&display=swap" rel="stylesheet">
<style>
  :root {
    --backdrop: #cfcfcf;
    --paper: #ffffff;
    --brand-blue: #0a3a9c;
    --brand-green: #8dc63f;
    --brand-cyan: #17a9e1;
    --card-green: #96c935;
    --text-grey: #555555;
    --divider: #c9c9c9;
  }
  * { margin: 0; padding: 0; box-sizing: border-box; }
  html, body {
    width: 1200px;
    height: 800px;
    overflow: hidden;
    background: var(--backdrop);
    font-family: "Roboto", Arial, sans-serif;
  }
  .stage {
    position: relative;
    width: 1200px;
    height: 800px;
  }
  .card {
    position: absolute;
    left: 320px;
    width: 560px;
    height: 320px;
    box-shadow: 0 6px 18px rgba(0,0,0,0.18);
    overflow: hidden;
  }
  .card--front { top: 60px; background: var(--paper); }
  .card--back  { top: 420px; }

  .brand {
    position: absolute;
    left: 40px;
    top: 0;
    width: 200px;
    height: 306px;
    display: flex;
    align-items: center;
    gap: 10px;
  }
  .brand__dot {
    width: 14px;
    height: 14px;
    border-radius: 50%;
    background: var(--brand-blue);
    flex: none;
  }
  .brand__name {
    font-size: 30px;
    font-weight: 700;
    color: var(--brand-blue);
    letter-spacing: -0.5px;
  }

  .divider {
    position: absolute;
    left: 258px;
    top: 100px;
    width: 1px;
    height: 120px;
    background: linear-gradient(to bottom, transparent, var(--divider) 30%, var(--divider) 70%, transparent);
  }

  .contact {
    position: absolute;
    left: 284px;
    top: 102px;
  }
  .contact__name {
    font-size: 21px;
    font-weight: 700;
    color: var(--brand-blue);
    line-height: 1.1;
  }
  .contact__role {
    font-size: 13px;
    font-weight: 700;
    color: var(--brand-green);
    margin-top: 3px;
    margin-bottom: 14px;
  }
  .contact__list { list-style: none; }
  .contact__item {
    display: flex;
    align-items: center;
    gap: 8px;
    font-size: 11.5px;
    color: var(--text-grey);
    line-height: 19px;
  }
  .contact__icon { width: 11px; height: 11px; flex: none; }

  .edge-band {
    position: absolute;
    left: 0;
    bottom: 0;
    width: 100%;
    height: 8px;
    display: flex;
  }
  .edge-band__results   { flex: 4; background: var(--brand-blue); }
  .edge-band__execution { flex: 3; background: var(--brand-green); }
  .edge-band__strategy  { flex: 3; background: var(--brand-cyan); }

  .back-fill {
    width: 100%;
    height: 100%;
    background: linear-gradient(135deg, #9fd23c 0%, var(--card-green) 60%, #8bbd2e 100%);
  }
</style>
</head>
<body>
<main class="stage">
  <section class="card card--front" aria-label="Business card front">
    <div class="brand">
      <span class="brand__dot"></span>
      <span class="brand__name">BrivoTerna</span>
    </div>
    <div class="divider"></div>
    <div class="contact">
      <h1 class="contact__name">Teodoro Vinsquel</h1>
      <p class="contact__role">CEO &amp; Founder</p>
      <ul class="contact__list">
        <li class="contact__item">
          <svg class="contact__icon" viewBox="0 0 12 12"><rect x="2.5" y="0.5" width="7" height="11" rx="1.2" fill="none" stroke="#0a3a9c" stroke-width="1.2"/><circle cx="6" cy="9.6" r="0.7" fill="#0a3a9c"/></svg>
          +34 655.803.912
        </li>
        <li class="contact__item">
          <svg class="contact__icon" viewBox="0 0 12 12"><rect x="0.5" y="2" width="11" height="8" rx="1" fill="#0a3a9c"/><path d="M1 2.6 L6 6.6 L11 2.6" fill="none" stroke="#fff" stroke-width="1"/></svg>
          teodoro.vinsquel@brivoterna-example.com
        </li>
        <li class="contact__item">
          <svg class="contact__icon" viewBox="0 0 12 12"><circle cx="6" cy="6" r="5.5" fill="#0a3a9c"/><path d="M0.8 6 H11.2 M6 0.5 C3.5 3 3.5 9 6 11.5 M6 0.5 C8.5 3 8.5 9 6 11.5" fill="none" stroke="#fff" stroke-width="0.8"/></svg>
          www.brivoterna-example.com
        </li>
      </ul>
    </div>
    <div class="edge-band">
      <span class="edge-band__results"></span>
      <span class="edge-band__execution"></span>
      <span class="edge-band__strategy"></span>
    </div>
  </section>

  <section class="card card--back" aria-label="Business card back">
    <div class="back-fill" role="img" aria-label="Green field with a repeating pattern of rising brand arrows and one white brand mark"></div>
  </section>
</main>
</body>
</html>
```